Stationery Design Project for Marketing Consultancy

I have started a new consultancy business and require the following elements to be designed using existing logo:
• Business card
• Letterhead
• Envelope (DL, C4, C5)
• Microsoft word template for report writing
• A4 Presentation Folder
• Powerpoint template
COPY FOR FRONT AND BACK OF BUSINESS CARD
logo
'Measurable Marketing. Epic Results' slogan (but no need to use existing lockup with logo)
name, B Bus. Mktg, Grad Dip Digital Mktg, CPM (post nominal abbreviations in smaller font)
mobile: 04XX-XXX-XXX (I will give details to the winner to add)
website: www.tolvarin.com.au
email: info@tolvarin.com.au
COPY FOR LETTERHEAD
Logo
Company Name
Please, submit your designs that include business card, letterhead and envelope. Once selected the winner will be asked to complete the project by creating the rest of the artwork.
FINAL FILES
Print ready files to be supplied as well as Indesign files so that minor amends can be made if necessary in future.
• Layered vectors in EPS & PDF
• Screen quality JPEG & PNGs
ABOUT THE BUSINESS: TOLVARIN
I work with clients to understand their business challenges, developing and executing measurable marketing strategies tied to key business metrics. Services include:
Services include:
• Business planning and business development
• Marketing and brand strategy
• Insight-driven integrated campaigns
• Loyalty programs and retention marketing
• Marketing automation
• Direct marketing (traditional and digital)
• Content strategy and development
Hi everyone,
Target Market(s)
Corporate decision makers (heads of marketing, general managers etc) and small to medium sized business owners. Predominately male aged 35+
Industry/Entity Type
Marketing
Requirements
Must have
- BRAND PERSONALITY
The successful design will communicate brand personality. I am a professional, results-driven entrepreneur, but want to show off my creative flair.
MEMORABILITY
Looking for a unique and eye-catching design. Am considering special printing effects (die cuts, letterpress, interactive elements, embossing, foiling etc) or a striking minimalist approach.
Nice to have
- I have a mission that could be incorporated on reverse if room -
Turning insights into actions & passion into profit.
Should not have
- Use of pink or green.

```html
<!DOCTYPE html>
<html lang="en">
<head>
<meta charset="utf-8">
<title>Tolvarin – Presentation Template</title>
<link rel="stylesheet" href="https://fonts.googleapis.com/css2?family=Open+Sans:wght@300;400;600;700&family=Carlito&family=Arimo:wght@400&display=swap">
<style>
  :root {
    --canvas: #e6e6e6;
    --slate: #434343;
    --slate-line: #5c5c5c;
    --paper: #f8f8f8;
    --gold: #f5b800;
    --grey-title: #6b6b6b;
    --grey-text: #333333;
    --grey-lead: #3c3c3c;
    --grey-soft: #777777;
    --grey-muted: #8c8c8c;
    --icon-orange: #f08a24;
    --white: #ffffff;
  }
  * { margin: 0; padding: 0; box-sizing: border-box; }
  html, body { width: 1200px; height: 900px; overflow: hidden; }
  body { background: var(--canvas); position: relative; font-family: "Arimo", Arial, sans-serif; }

  .slide { position: absolute; width: 583px; height: 437px; overflow: hidden; box-shadow: 0 0 3px rgba(0,0,0,.18); }
  .slide--welcome { left: 10px; top: 12px; background: var(--slate); }
  .slide--intro { left: 605px; top: 12px; background: var(--paper); }
  .slide--contact { left: 10px; top: 457px; background: var(--paper); }
  .slide--thanks { left: 605px; top: 457px; background: var(--slate); }

  /* brand mark stand-in */
  .brand { position: absolute; left: 0; right: 0; text-align: center; color: var(--white); font-family: "Open Sans", sans-serif; }
  .brand__dot { display: block; margin: 0 auto 10px; border-radius: 50%; background: var(--white); }
  .brand__name { font-weight: 700; letter-spacing: 1px; line-height: 1; }

  .slide--welcome .brand { top: 62px; }
  .slide--welcome .brand__dot { width: 64px; height: 64px; }
  .slide--welcome .brand__name { font-size: 30px; }

  .welcome__title { position: absolute; top: 238px; left: 0; right: 0; text-align: center; font-family: "Open Sans", sans-serif; font-weight: 700; font-size: 50px; color: var(--gold); letter-spacing: -0.5px; }
  .welcome__sub { position: absolute; top: 310px; left: 0; right: 0; text-align: center; font-family: "Arimo", sans-serif; font-size: 19px; color: #6a6a6a; letter-spacing: .3px; }

  .slide__rule { position: absolute; left: 0; right: 0; top: 416px; height: 3px; background: var(--slate-line); }
  .slide__url { position: absolute; left: 0; right: 0; top: 421px; text-align: center; font-size: 10.5px; color: #aaaaaa; }
  .slide--intro .slide__rule, .slide--contact .slide__rule { background: #555555; }
  .slide--intro .slide__url, .slide--contact .slide__url { color: #555555; }

  .slide__title { position: absolute; left: 27px; top: 20px; font-family: "Open Sans", sans-serif; font-weight: 700; font-size: 35px; letter-spacing: -2.2px; }
  .slide__title .muted { color: var(--grey-title); }
  .slide__title .accent { color: var(--gold); }
  .slide__lead { position: absolute; left: 29px; top: 73px; font-size: 13.5px; color: var(--grey-lead); }

  .copy { position: absolute; font-family: "Carlito", Calibri, sans-serif; font-size: 8px; line-height: 10.6px; color: var(--grey-text); }
  .copy p { text-indent: 10px; margin-bottom: 10px; }
  .divider { position: absolute; width: 0; border-left: 2px dotted #888888; }
  .divider--light { border-left: 1px dotted #999999; }

  .intro__col--left { left: 37px; top: 124px; width: 195px; }
  .intro__col--right { left: 333px; top: 124px; width: 190px; }
  .slide--intro .divider { left: 289px; top: 124px; height: 200px; }

  .contact__copy { left: 28px; top: 148px; width: 195px; }
  .slide--contact .divider { left: 245px; top: 122px; height: 116px; }
  .contact__list { position: absolute; left: 268px; top: 156px; list-style: none; font-size: 13px; color: #444444; }
  .contact__list li { display: flex; align-items: center; height: 18px; }
  .contact__list svg { width: 10px; height: 10px; margin-right: 12px; flex: none; }

  /* footer band */
  .footer { position: absolute; left: 0; right: 0; top: 374px; height: 42px; background: linear-gradient(180deg, #ffffff 0%, #f0f0f0 55%, #dcdcdc 100%); border-top: 1px solid #e2e2e2; }
  .footer__brand { position: absolute; left: 38px; top: 5px; width: 50px; text-align: center; font-family: "Open Sans", sans-serif; color: #333333; }
  .footer__dot { display: block; width: 16px; height: 16px; border-radius: 50%; background: #333333; margin: 0 auto 2px; }
  .footer__name { font-size: 8.5px; font-weight: 700; letter-spacing: .3px; }
  .footer__sep { position: absolute; top: 11px; height: 16px; border-left: 1px dotted #999999; }
  .footer__sep--a { left: 150px; }
  .footer__sep--b { left: 460px; }
  .footer__mission { position: absolute; left: 178px; top: 13px; font-size: 11.5px; color: var(--grey-soft); }
  .footer__page { position: absolute; left: 516px; top: 14px; font-size: 9px; color: #333333; }

  .slide--thanks .brand { top: 68px; }
  .slide--thanks .brand__dot { width: 58px; height: 58px; }
  .slide--thanks .brand__name { font-size: 24px; }
  .thanks__title { position: absolute; top: 222px; left: 0; right: 0; text-align: center; font-family: "Open Sans", sans-serif; font-weight: 700; font-size: 42px; color: var(--grey-muted); }
</style>
</head>
<body>

<section class="slide slide--welcome">
  <div class="brand">
    <span class="brand__dot"></span>
    <div class="brand__name">TOLVARIN</div>
  </div>
  <h1 class="welcome__title">Welcome</h1>
  <p class="welcome__sub">TO OUR PRESENTATION</p>
  <div class="slide__rule"></div>
  <p class="slide__url">www.tolvarin.com.au</p>
</section>

<section class="slide slide--intro">
  <h2 class="slide__title"><span class="muted">Small </span><span class="accent">INTRO</span></h2>
  <p class="slide__lead">Here goes little description, usually about topic or company</p>
  <div class="copy intro__col--left">
    <p>We start by listening to your goals, your customers and your numbers, then build a clear plan that links every single campaign to a business result you can track, measure and report on each month, so you always know where your budget goes and what it returns.</p>
    <p>Insight comes first. We review your data, study the market and find the moments where a small change can lift sales, loyalty and retention across every channel you use today.</p>
    <p>Then we act. Campaigns are planned, launched and tested with care, and every report shows what worked, what did not and what we will try next to grow profit for you.</p>
  </div>
  <div class="divider"></div>
  <div class="copy intro__col--right">
    <p>Our team blends sharp strategy with real creative flair, so your brand looks bold and polished while the numbers keep moving in the right direction every quarter.</p>
    <p>From business planning to marketing automation, content and direct marketing, we cover each step of the journey. You get one partner, one plan and one clear view of results, with honest advice and simple reports that help you decide what comes next. We keep things practical, focused and easy to follow, so every dollar works harder for your business.</p>
  </div>
  <footer class="footer">
    <div class="footer__brand"><span class="footer__dot"></span><span class="footer__name">TOLVARIN</span></div>
    <span class="footer__sep footer__sep--a"></span>
    <span class="footer__mission">Turning insights into action and passion into profit</span>
    <span class="footer__sep footer__sep--b"></span>
    <span class="footer__page">2</span>
  </footer>
  <div class="slide__rule"></div>
  <p class="slide__url">www.tolvarin.com.au</p>
</section>

<section class="slide slide--contact">
  <h2 class="slide__title"><span class="accent">CONTACT US</span></h2>
  <p class="slide__lead">Here goes little description, usually about topic or company</p>
  <div class="copy contact__copy">
    <p>Call, email or visit our website to book a free first meeting. We will talk about your goals, your customers and your current results, then show how measurable marketing can deliver real growth for you.</p>
  </div>
  <div class="divider divider--light"></div>
  <ul class="contact__list">
    <li>
      <svg viewBox="0 0 10 10" aria-hidden="true"><rect x="2" y="0.5" width="6" height="9" rx="1.2" fill="var(--icon-orange)"/><rect x="3" y="1.8" width="4" height="5.5" fill="#fff"/></svg>
      04XX-XXX-XXX
    </li>
    <li>
      <svg viewBox="0 0 10 10" aria-hidden="true"><rect x="0.5" y="2" width="9" height="6.5" rx="0.8" fill="var(--icon-orange)"/><path d="M1 2.5 L5 5.8 L9 2.5" stroke="#fff" stroke-width="1" fill="none"/></svg>
      info@tolvarin.com.au
    </li>
    <li>
      <svg viewBox="0 0 10 10" aria-hidden="true"><circle cx="5" cy="5" r="4.5" fill="var(--icon-orange)"/><ellipse cx="5" cy="5" rx="1.8" ry="4.3" stroke="#fff" stroke-width=".8" fill="none"/><line x1="0.6" y1="5" x2="9.4" y2="5" stroke="#fff" stroke-width=".8"/></svg>
      www.tolvarin.com.au
    </li>
  </ul>
  <footer class="footer">
    <div class="footer__brand"><span class="footer__dot"></span><span class="footer__name">TOLVARIN</span></div>
    <span class="footer__sep footer__sep--a"></span>
    <span class="footer__mission">Turning insights into action and passion into profit</span>
    <span class="footer__sep footer__sep--b"></span>
    <span class="footer__page">6</span>
  </footer>
  <div class="slide__rule"></div>
  <p class="slide__url">www.tolvarin.com.au</p>
</section>

<section class="slide slide--thanks">
  <div class="brand">
    <span class="brand__dot"></span>
    <div class="brand__name">TOLVARIN</div>
  </div>
  <h2 class="thanks__title">Thank you!</h2>
  <div class="slide__rule"></div>
  <p class="slide__url">www.tolvarin.com.au</p>
</section>

</body>
</html>
```